Bluecrest Learning Corps by graduating students from college in two years

Based on the logo design, create stationary and business cards for
Dr. Venrel T Oskamp, CEO, (703) 482-1736
and Marisa Deltoft, Respresentative, (301) 647-2208
Address: 4719 Pellham Court, Brackenridge Station, VA 22418
Incorporate elelments of the logo

Target Market(s)

USA

Font styles to use
Other font styles liked:
• match with the logo type style

```html
<!DOCTYPE html>
<html lang="en">
<head>
<meta charset="utf-8">
<title>Bluecrest Learning Corps — Letterhead</title>
<link href="https://fonts.googleapis.com/css2?family=Arimo:wght@400;700&family=Questrial&display=swap" rel="stylesheet">
<style>
  :root {
    --backdrop: #e4e5e7;
    --paper: #ffffff;
    --navy: #1c2a6b;
    --gold: #f2c230;
    --ink: #3b3b3d;
    --muted: #555558;
    --rule: #6a6a6e;
    --tint: #eef0f4;
  }
  * { margin: 0; padding: 0; box-sizing: border-box; }
  html, body { width: 1200px; height: 960px; overflow: hidden; }
  body {
    background: var(--backdrop);
    font-family: "Arimo", Arial, sans-serif;
    color: var(--ink);
    position: relative;
  }
  .letterhead {
    position: absolute;
    left: 252px; top: 30px;
    width: 696px; height: 900px;
    background: var(--paper);
    box-shadow: 0 6px 24px rgba(0,0,0,0.12);
    overflow: hidden;
  }
  .backdrop-mark {
    position: absolute;
    right: 40px; bottom: 40px;
    width: 280px; height: 200px;
    background: linear-gradient(135deg, var(--tint), #f5f6f9);
    border-radius: 10px;
    z-index: 0;
  }
  .masthead {
    position: absolute;
    left: 40px; top: 44px; right: 40px;
    height: 120px;
    z-index: 1;
  }
  .brand {
    position: absolute;
    left: 0; top: 50px;
    display: flex; align-items: center; gap: 10px;
    width: 170px;
  }
  .brand-dot {
    flex: none;
    width: 22px; height: 22px; border-radius: 50%;
    background: var(--gold);
  }
  .brand-name {
    font-weight: 700; font-size: 15px; line-height: 1.2;
    color: var(--navy);
  }
  .masthead-rule {
    position: absolute;
    left: 180px; right: 0; top: 76px;
    height: 1px; background: var(--rule);
  }
  .contacts {
    position: absolute;
    left: 190px; right: 0; top: 14px;
    display: flex; align-items: flex-start;
  }
  .contact { padding: 0 16px; font-size: 10.5px; line-height: 1.3; color: var(--muted); white-space: nowrap; }
  .contact:first-child { padding-left: 0; }
  .contact + .contact { border-left: 1px solid var(--gold); }
  .contact-name { font-weight: 700; font-size: 13px; color: var(--navy); }
  .contact-phone { display: flex; align-items: center; gap: 4px; }
  .contact-phone svg { width: 10px; height: 10px; fill: var(--gold); }
  .letter {
    position: absolute;
    left: 190px; top: 250px;
    width: 440px;
    z-index: 1;
  }
  .salutation {
    font-family: "Questrial", "Century Gothic", sans-serif;
    font-weight: 700; font-size: 17px; color: var(--ink);
    margin-left: -28px; margin-bottom: 16px;
  }
  .letter p {
    font-size: 11.5px; line-height: 15px; color: var(--ink);
    margin-bottom: 15px;
  }
  .closing {
    font-family: "Questrial", "Century Gothic", sans-serif;
    font-weight: 700; font-size: 11px;
    margin-top: 22px;
  }
  .signature {
    margin-top: 14px; margin-left: 36px;
    width: 140px; height: 40px;
    background: linear-gradient(90deg, #f0f0f1, #f7f7f8);
    border-radius: 4px;
  }
</style>
</head>
<body>
  <main class="letterhead">
    <div class="backdrop-mark" role="img" aria-label="Faint brand decoration in the lower corner"></div>

    <header class="masthead">
      <div class="brand">
        <span class="brand-dot"></span>
        <span class="brand-name">Bluecrest Learning Corps</span>
      </div>
      <div class="masthead-rule"></div>
      <div class="contacts">
        <div class="contact">
          <div class="contact-name">Dr. Venrel T Oskamp</div>
          <div>CEO</div>
          <div class="contact-phone">
            <svg viewBox="0 0 10 10"><path d="M1 3c0-1 1-2 4-2s4 1 4 2v1H7V3H3v1H1zM2 5h6l1 4H1z"/></svg>
            (703) 482-1736
          </div>
        </div>
        <div class="contact">
          <div class="contact-name">Marisa Deltoft</div>
          <div>Respresentative</div>
          <div class="contact-phone">
            <svg viewBox="0 0 10 10"><path d="M1 3c0-1 1-2 4-2s4 1 4 2v1H7V3H3v1H1zM2 5h6l1 4H1z"/></svg>
            (301) 647-2208
          </div>
        </div>
        <div class="contact">
          <div>4719 Pellham Court</div>
          <div>Brackenridge Station</div>
          <div>VA 22418</div>
        </div>
      </div>
    </header>

    <section class="letter">
      <h1 class="salutation">Dear Mr. Calloway,</h1>
      <p>Lorem ipsum dolor sit amet, consectetuer adipiscing elit, sed diam nonummy nibh euismod tincidunt ut laoreet dolore magna aliquam erat volutpat. Ut wisi enim ad minim veniam, quis nostrud exerci tationmcorper suscipit lobortis nisl ut aliquip ex ea commodo consequat. Duis autem vel eum iriure dolor in hendrerit in vulputate velit esse molestie consequat, vel illum dolore eu feugiat</p>
      <p>Rorem ipsum dolor sit amet, consectetuer adipiscing elit, sed diam nonummy nibh euismod tincidunt ut laoreet dolore magna aliquam erat volutpat. Ut wisi enim ad minim veniam, quis nostrud exerci tationmcorper suscipit lobortis nisl ut aliquip ex ea commodo consequat. Duis autem vel eum iriure dolor in hendrerit in vulputate velit esse molest</p>
      <p>Dorem ipsum dolor sit amet, consectetuer adipiscing elit, sed diam nonummy nibh euismod tincidunt ut laoreet dolore magna aliquam erat volutpat. Ut wisi enim ad minim veniam, quis nostrud exerci tationmcorper suscipit lobortis nisl ut aliquip ex ea commodo consequat. Duis autem vel eum iriure dolor in hendrerit in suscipit lobortis nisl ut aliquip ex ea commodo consequat, vel illum vulputate velit esse molestie consequat, vel illum</p>
      <p>Sorem ipsum dolor sit amet, consectetuer adipiscing elit, sed diam nonummy nibh euismod tincidunt ut laoreet dolore magna aliquam erat volutpat. Ut wisi enim ad minim veniam, quis nostrud exerci tationmcorper suscipit lobortis nisl ut aliquip ex ea commodo consequat. Duis autem vel eum iriure dolor in</p>
      <div class="closing">Sincerely,</div>
      <div class="signature" role="img" aria-label="Handwritten signature"></div>
    </section>
  </main>
</body>
</html>
```